KVR - Redesign (PSD Files Only)

Requirements for the site:

1. We need our logo recreated, please use the same design and change colors to work on a white background

2. The site is a "Wizard" based site, that takes the customer through the process of creating a unique web presence that suits there needs

3.Colors Needed - Main "Dark Blue" Secondary = "Dark Grey" -Other = "Light Grey and White"

4.We need a CRISP CLEAN DESIGN, simple design

5.Wireframes are a general layout and may be modified by you to enhance the design

6. We want a complete web 5.0 look with big buttons and text boxes

7.The more personality the better

8. Current Site brightpolehub.example

9.See attachments for wireframes

10. Designer should deliver PSD files, no coding is required

11. The portfolio wireframe, should look like the design of the artflockly portfolio template
Updates

KEEP IT SIMPLE.,.....

We like the quillmark scaffold style of designs

```html
<!DOCTYPE html>
<html lang="en">
<head>
<meta charset="utf-8">
<title>About Us – Kivera Studios Inc</title>
<link href="https://fonts.googleapis.com/css2?family=Dosis:wght@400;600;700&family=Open+Sans:ital,wght@0,400;0,600;1,400&display=swap" rel="stylesheet">
<style>
:root{
  --navy:#0b3563;
  --blue:#1c3f6b;
  --nav-active:#1e4a80;
  --dark:#1a1a1a;
  --footer:#222222;
  --footer-strip:#1b1b1b;
  --grey-line:#dfe3e7;
  --text:#1a1a1a;
  --muted:#666;
  --orange-top:#ffa033;
  --orange-bottom:#ff7a00;
}
*{margin:0;padding:0;box-sizing:border-box}
html,body{width:1200px;height:974px;overflow:hidden;background:#fff}
body{position:relative;font-family:"Open Sans",sans-serif;color:var(--text)}
.abs{position:absolute}
.topbar{left:0;top:0;width:1200px;height:23px;background:var(--dark)}
.header-shape{left:0;top:0}
.brand{left:150px;top:26px;width:129px;text-align:center;color:#fff;font-family:"Open Sans",sans-serif;font-weight:600}
.brand .mark{font-size:26px;letter-spacing:2px;line-height:30px}
.brand .name{font-size:9px;line-height:12px}
.nav{left:300px;top:0;height:46px;display:flex;font-family:"Dosis",sans-serif;font-size:21px;color:#fff}
.nav a{color:#fff;text-decoration:none;height:46px;line-height:46px;padding:0 12px}
.nav a.active{background:var(--nav-active);padding:0 14px}
.social{display:flex;gap:8px}
.social span{display:block;border-radius:50%;background:#fff}
.head-social{left:704px;top:10px}
.head-social span{width:26px;height:26px}
.phone{display:flex;align-items:center;gap:5px;font-family:"Dosis",sans-serif;color:#fff}
.head-phone{left:883px;top:7px;font-size:26px;line-height:32px}
h1{left:128px;top:128px;font-family:"Dosis",sans-serif;font-weight:700;font-size:35px;color:var(--blue);line-height:44px}
.title-rule{left:128px;top:180px}
.photo-frame{left:128px;top:227px;width:383px;height:273px;border:1px solid #ccc;padding:7px;background:#fff}
.photo{width:100%;height:100%;background:linear-gradient(135deg,#e9ecef 0%,#d9dde0 40%,#a7a6a3 70%,#d6c6ae 100%)}
h2{left:537px;top:234px;font-weight:600;font-size:26px;color:var(--navy);line-height:34px}
.sub-rule{left:537px;top:275px;width:534px;height:3px;background:var(--grey-line)}
.bio{left:537px;top:293px;width:538px;font-size:13.6px;line-height:17.1px}
.sep{left:128px;top:543px;width:943px;height:3px;background:var(--grey-line)}
.btn{display:flex;align-items:center;justify-content:center;background:linear-gradient(var(--orange-top),var(--orange-bottom));color:#fff;font-family:"Dosis",sans-serif;font-weight:700;font-size:27px;border:1px solid #e46b00}
.btn-main{left:128px;top:567px;width:243px;height:54px}
.tagline{left:393px;top:571px;font-style:italic;font-size:15.4px;line-height:19px;color:var(--muted)}
.banner{left:129px;top:659px;width:941px;height:52px;background:var(--navy);display:flex;align-items:center;padding-left:24px;gap:14px;color:#fff;font-style:italic;font-size:15.6px}
footer{left:0;top:756px;width:1200px;height:218px;background:var(--footer)}
.foot-links{left:129px;top:797px;font-size:12.3px;line-height:19px;color:#fff}
.foot-links .dot{padding:0 6px}
.foot-social{left:498px;top:794px;gap:8px}
.foot-social span{width:38px;height:38px}
.foot-phone{left:498px;top:837px;font-size:25px;line-height:30px}
.btn-foot{left:828px;top:794px;width:243px;height:54px}
.strip{left:129px;top:879px;width:949px;height:53px;background:var(--footer-strip)}
.badge{left:129px;top:879px;width:156px;height:53px;background:#fff;display:flex}
.badge i{display:block;width:53px;height:53px;background:#3f7ee8}
</style>
</head>
<body>
<div class="abs topbar"></div>
<svg class="abs header-shape" width="1200" height="100" viewBox="0 0 1200 100" aria-hidden="true">
  <polygon points="117,23 129,23 129,0 1071,0 1071,23 1087,23 1074,46 129,46" fill="#1a1a1a"/>
  <path d="M150 0 H279 V87 Q214 102 150 87 Z" fill="#1a1a1a"/>
</svg>
<div class="abs brand"><div class="mark">KVR</div><div class="name">Kivera Studios Inc</div></div>
<nav class="abs nav">
  <a href="#">Home</a><a href="#" class="active">About Us</a><a href="#">Portfolio</a><a href="#">Contact Us</a>
</nav>
<div class="abs social head-social"><span></span><span></span><span></span><span></span></div>
<div class="abs phone head-phone">
  <svg width="14" height="20" viewBox="0 0 14 20"><path d="M3 1 L6 5 L4 8 Q6 12 9 14 L11 12 L14 15 L11 19 Q2 15 0 4 Z" fill="#fff"/></svg>1800-555-0142
</div>

<h1 class="abs">About Our Owner</h1>
<svg class="abs title-rule" width="943" height="10" viewBox="0 0 943 10" aria-hidden="true">
  <rect x="0" y="4" width="28" height="2" fill="#1c3f6b"/>
  <circle cx="35" cy="5" r="4" fill="#1c3f6b"/>
  <rect x="43" y="4" width="900" height="3" fill="#1c3f6b"/>
</svg>

<div class="abs photo-frame"><div class="photo" role="img" aria-label="Photo of the company owner at his desk with a computer in a bright studio"></div></div>
<h2 class="abs">CEO - MARCUS HALE</h2>
<div class="abs sub-rule"></div>
<p class="abs bio">Lorem ipsum dolor sit amet, consectetur adipiscing elit. In fermentum dolor non augue pretium egestas. Donec sem eros, tincidunt at congue ut, posuere sit amet est. Vivamus scelerisque viverra odio sit amet laoreet. Ut nec neque non justo rutrum tempor lobortis eu ante. Aliquam sagittis, nibh quis commodo auctor, risus mauris laoreet lectus, id facilisis libero odio nec enim. Sed id ligula adipiscing purus lacinia aliquet. Sed eu est non nisl vehicula bibendum congue sit amet enim. Lorem ipsum dolor sit amet, consectetur adipiscing elit. In fermentum dolor non augue pretium egestas. Donec sem eros, tincidunt at congue ut, posuere sit amet est. Vivamus scelerisque viverra odio sit amet laoreet. Ut nec neque non justo rutrum tempor lobortis eu ante. Aliquam sagittis, nibh quis commodo auctor</p>

<div class="abs sep"></div>
<a class="abs btn btn-main">Request Consultant</a>
<p class="abs tagline">Our web professionals will contact<br>you to discuss your project</p>

<div class="abs banner">
  <svg width="29" height="29" viewBox="0 0 29 29" aria-hidden="true"><circle cx="14.5" cy="14.5" r="14.5" fill="#fff"/><circle cx="15.5" cy="8" r="2.2" fill="#0b3563"/><path d="M12 12 H17 L15 22 H17 L16.5 23.5 H11 L13 13.5 H11.5 Z" fill="#0b3563"/></svg>
  As your full service marketing partner, we will deliver and end to end marketing solution for your business.
</div>

<footer class="abs"></footer>
<div class="abs foot-links">
  Home<span class="dot">.</span>About Us<span class="dot">.</span>Portfolio<span class="dot">.</span>Contact Us<br>
  Copyright © 2014 Kivera Studios Inc - All Right Reserved<br>
  www.brightpolehub.example
</div>
<div class="abs social foot-social"><span></span><span></span><span></span><span></span></div>
<div class="abs phone foot-phone">
  <svg width="14" height="20" viewBox="0 0 14 20"><path d="M3 1 L6 5 L4 8 Q6 12 9 14 L11 12 L14 15 L11 19 Q2 15 0 4 Z" fill="#fff"/></svg>1800-555-0142
</div>
<a class="abs btn btn-foot">Request Consultant</a>
<div class="abs strip"></div>
<div class="abs badge" role="img" aria-label="Partner badge"><i></i></div>
</body>
</html>
```